Real Estate Company Looking for Business Card Designs for 3 Executives

Hello!
Thanks so much for considering our project! We are a real estate investment company located in Edmonton, Alberta called Bellhaven Group of Companies. We invest/develop both commercial and residential real estate and are looking to create 3 DOUBLE-SIDED business cards for 3 top executives in the company! (for some reason it won't let us select the double-sided option, but yes, the cards are double sided and would be happy to tip extra)

We have certain guidelines that we want our business cards to for sure follow - the back of the Business card has to be the Black Background Version of the Logo which has already been designed and linked as a file (first file). We want the entire back of the card to simply just be the black background logo. In terms of the front of the card, would like to see a smaller version of the white background logo (linked as the second file) in the top left hand corner - of course, feel free to get creative and we can make revisions together along the way! and Then after that, just text. We want the card to be sharp, clean, easy on the eyes and highly professional looking. We would like the card to include the Full name of the Company (Bellhaven Group of Companies), Name of the Person, Title, Phone, Email. If possible please provide the front part of the card for 3 people:

1) Bellhaven Group of Companies, Liora Quenby, Chief Financial Officer, 780-555-0142, lioraquenby@bellhavengroup.example

2) Bellhaven Group of Companies, Tobias Quenby, Chief Executive Officer, 780-555-0187, tobiasquenby@bellhavengroup.example

3) Bellhaven Group of Companies, Rui Delcourt, Chief Operations Officer, 587-555-0163, ruidelcourt@bellhavengroup.example

Thank you so much for considering our project & we look forward to seeing your designs!

```html
<!DOCTYPE html>
<html lang="en">
<head>
<meta charset="utf-8">
<title>Bellhaven Group of Companies – Business Card</title>
<link rel="stylesheet" href="https://fonts.googleapis.com/css2?family=Tinos:wght@400;700&family=Arimo:wght@400&display=swap">
<style>
  :root {
    --backdrop: #cfd2d3;
    --card-light: #f4f4f2;
    --card-dark: #141414;
    --ink: #111111;
    --ink-soft: #2a2a2a;
    --paper-ink: #f1f1f1;
    --rule: #3a3a3a;
  }
  * { box-sizing: border-box; margin: 0; padding: 0; }
  html, body { width: 1200px; height: 905px; overflow: hidden; }
  body {
    background: var(--backdrop);
    font-family: "Arimo", Arial, sans-serif;
    color: var(--ink);
    position: relative;
  }
  .card {
    position: absolute;
    left: 260px;
    width: 680px;
    height: 388px;
    border-radius: 4px;
    box-shadow: 0 10px 28px rgba(0,0,0,0.18);
  }
  .card--front { top: 48px; background: var(--card-light); }
  .card--back { top: 470px; background: var(--card-dark); }

  .brand {
    font-family: "Tinos", "Times New Roman", serif;
    font-weight: 400;
    text-transform: uppercase;
    letter-spacing: 0.28em;
    display: flex;
    align-items: center;
    gap: 10px;
  }
  .brand__dot {
    width: 10px; height: 10px; border-radius: 50%;
    background: currentColor; flex: none;
  }
  .card--front .brand {
    position: absolute;
    left: 44px; top: 150px;
    width: 250px;
    font-size: 15px;
    line-height: 1.5;
    color: var(--ink);
  }
  .divider {
    position: absolute;
    left: 318px; top: 92px;
    width: 1px; height: 204px;
    background: var(--rule);
  }
  .details {
    position: absolute;
    left: 346px; top: 110px;
    width: 310px;
  }
  .person__name {
    font-family: "Tinos", "Times New Roman", serif;
    font-weight: 700;
    font-size: 27px;
    letter-spacing: 0.01em;
    text-transform: uppercase;
    line-height: 1.05;
  }
  .person__title {
    font-size: 17px;
    color: var(--ink-soft);
    margin-top: 4px;
  }
  .contact {
    list-style: none;
    margin-top: 24px;
    font-size: 14.5px;
  }
  .contact li {
    display: flex;
    align-items: center;
    gap: 8px;
    height: 27px;
    white-space: nowrap;
  }
  .contact svg { width: 13px; height: 13px; flex: none; fill: var(--ink); }

  .card--back .brand {
    position: absolute;
    inset: 0;
    justify-content: center;
    color: var(--paper-ink);
    font-size: 24px;
    letter-spacing: 0.3em;
  }
</style>
</head>
<body>
  <section class="card card--front" aria-label="Business card front">
    <div class="brand"><span class="brand__dot"></span><span>Bellhaven Group of Companies</span></div>
    <div class="divider"></div>
    <div class="details">
      <h1 class="person__name">Tobias Quenby</h1>
      <p class="person__title">Chief Executive Officer</p>
      <ul class="contact">
        <li>
          <svg viewBox="0 0 24 24" aria-hidden="true"><path d="M6.6 10.8a15.1 15.1 0 0 0 6.6 6.6l2.2-2.2a1 1 0 0 1 1-.25 11.4 11.4 0 0 0 3.6.57 1 1 0 0 1 1 1V20a1 1 0 0 1-1 1A17 17 0 0 1 3 4a1 1 0 0 1 1-1h3.5a1 1 0 0 1 1 1c0 1.25.2 2.45.57 3.57a1 1 0 0 1-.25 1z"/></svg>
          <span>780-555-0187</span>
        </li>
        <li>
          <svg viewBox="0 0 24 24" aria-hidden="true"><path d="M2 5h20v14H2z M4 7v.5l8 5.5 8-5.5V7l-8 5.5z" fill-rule="evenodd"/></svg>
          <span>tobiasquenby@bellhavengroup.example</span>
        </li>
        <li>
          <svg viewBox="0 0 24 24" aria-hidden="true"><path d="M12 2a10 10 0 1 0 0 20 10 10 0 0 0 0-20zm0 2c1 0 2.3 2.2 2.7 6H9.3C9.7 6.2 11 4 12 4zM4.1 13h3.2c.1 2 .5 3.8 1.1 5.2A8 8 0 0 1 4.1 13zm0-2a8 8 0 0 1 4.3-5.2c-.6 1.4-1 3.2-1.1 5.2zm5.2 2h5.4c-.4 3.8-1.7 7-2.7 7s-2.3-3.2-2.7-7zm7.4 0h3.2a8 8 0 0 1-4.3 5.2c.6-1.4 1-3.2 1.1-5.2zm0-2c-.1-2-.5-3.8-1.1-5.2a8 8 0 0 1 4.3 5.2z"/></svg>
          <span>www.bellhavengroup.example</span>
        </li>
      </ul>
    </div>
  </section>

  <section class="card card--back" aria-label="Business card back">
    <div class="brand"><span class="brand__dot"></span><span>Bellhaven Group of Companies</span></div>
  </section>
</body>
</html>
```